Social Media Graphics - Oakline Push REVISED

Create 6-7 individual social media graphics (square size) to encourage folks to join our online course called:

The Harvest Ledger Circle
How to Launch a Multi-Million Business From Scratch
Sign Up Today!

IMPORTANT: Make the largest and most prominent text on the graphic be: How to Launch a Multi-Million Business From Scratch

For the color scheme of the graphics, let's try a blue color palette; make sure the graphics appeal to both men and women

Make sure each graphic contains 1 of the 3 pics attached (crop pic as needed); and make sure one of the graphics is all TEXT only.

Target Market(s)

men and women looking to start a business

Industry/Entity Type

Entrepreneurship

Colors
0054AA
0677BA
7BADD7
CADEEF
E8F1F8

Requirements
Must have
• All the text and use the 3 pics provided; one graphic can be all text; Simple, modern design that's easy to read

```html
<!DOCTYPE html>
<html lang="en">
<head>
<meta charset="UTF-8">
<title>The Harvest Ledger Circle – Sign Up</title>
<link href="https://fonts.googleapis.com/css2?family=Lora:ital,wght@1,700&display=swap" rel="stylesheet">
<style>
  :root {
    --blue-deep: #0054AA;
    --blue-mid: #0677BA;
    --blue-soft: #7BADD7;
    --blue-pale: #CADEEF;
    --blue-mist: #E8F1F8;
    --violet-base: #3a3f95;
    --host-pink: #d9336a;
    --host-pink-dark: #a8214f;
    --host-black: #16161f;
    --white: #ffffff;
  }
  html, body {
    margin: 0;
    padding: 0;
    width: 1200px;
    height: 1200px;
    overflow: hidden;
    background: var(--blue-deep);
  }
  .poster {
    position: relative;
    width: 1200px;
    height: 1200px;
    overflow: hidden;
    background:
      radial-gradient(ellipse at 50% 55%, var(--blue-mid) 0%, rgba(6,119,186,0) 60%),
      linear-gradient(180deg, #0a58b4 0%, #0a62b8 55%, #2a4fa6 82%, var(--violet-base) 100%);
    font-family: "Lora", Georgia, serif;
    font-style: italic;
    font-weight: 700;
    text-align: center;
  }
  .corner-orbs {
    position: absolute;
    inset: 0;
    width: 1200px;
    height: 1200px;
    z-index: 2;
  }
  .headline {
    position: absolute;
    top: 98px;
    left: 0;
    width: 100%;
    margin: 0;
    color: var(--white);
    font-weight: 700;
    font-size: 64px;
    line-height: 80px;
    text-transform: uppercase;
  }
  .course-name {
    position: absolute;
    top: 404px;
    left: 0;
    width: 100%;
    margin: 0;
    color: var(--blue-pale);
    font-size: 60px;
    line-height: 76px;
  }
  .hosts-photo {
    position: absolute;
    left: 242px;
    top: 522px;
    width: 680px;
    height: 678px;
    z-index: 1;
    border-radius: 190px 190px 0 0;
    background:
      linear-gradient(180deg, rgba(30,30,45,0.85) 0%, rgba(30,30,45,0) 26%),
      linear-gradient(90deg, var(--host-pink) 0%, var(--host-pink-dark) 46%, var(--host-black) 50%, var(--host-black) 100%);
    -webkit-mask-image: linear-gradient(180deg, #000 0%, #000 72%, rgba(0,0,0,0.35) 100%);
    mask-image: linear-gradient(180deg, #000 0%, #000 72%, rgba(0,0,0,0.35) 100%);
  }
  .cta-button {
    position: absolute;
    left: 364px;
    top: 1033px;
    width: 483px;
    height: 104px;
    z-index: 3;
    box-sizing: border-box;
    border-radius: 16px;
    background: var(--blue-deep);
    color: var(--blue-mist);
    font-size: 46px;
    line-height: 104px;
    text-decoration: none;
  }
</style>
</head>
<body>
  <main class="poster">
    <h1 class="headline">How to Launch a<br>Multi-Million Business<br>From Scratch</h1>

    <p class="course-name">The Harvest Ledger Circle</p>

    <div class="hosts-photo" role="img" aria-label="Photo of the two course hosts smiling, a woman in a pink top with arms crossed and a man in a black shirt and vest"></div>

    <svg class="corner-orbs" viewBox="0 0 1200 1200" aria-hidden="true">
      <circle cx="-20" cy="1060" r="230" fill="rgba(123,173,215,0.12)" stroke="rgba(202,222,239,0.25)" stroke-width="2"/>
      <circle cx="90" cy="1230" r="200" fill="rgba(123,173,215,0.10)" stroke="rgba(202,222,239,0.2)" stroke-width="2"/>
      <circle cx="1220" cy="1060" r="230" fill="rgba(123,173,215,0.12)" stroke="rgba(202,222,239,0.25)" stroke-width="2"/>
      <circle cx="1110" cy="1230" r="200" fill="rgba(123,173,215,0.10)" stroke="rgba(202,222,239,0.2)" stroke-width="2"/>
    </svg>

    <a class="cta-button" href="#signup">Sign Up Today!</a>
  </main>
</body>
</html>
```